RTavenor Business Cards & Letterhead

I have a logo but need a design for some new business cards. We are a Design-Build Firm that specializes in the design and construction of commercial projects.
the cards need to be professional. no cartoon stuff.
i would like to have the cards in AI format so I can update the card as needed. Logo is provided.
Our Address is: 4187 Marlowe Ct. Apex, North Carolina 27614

```html
<!DOCTYPE html>
<html lang="en">
<head>
<meta charset="utf-8">
<title>RTavenor Business Cards &amp; Letterhead</title>
<link href="https://fonts.googleapis.com/css2?family=Barlow:wght@400;500;600;700&display=swap" rel="stylesheet">
<style>
  :root {
    --backdrop: #979797;
    --paper: #ffffff;
    --brand-blue: #0f6fa6;
    --brand-blue-deep: #08507f;
    --brand-blue-light: #1a78b2;
    --ink: #4a4a4a;
    --ink-dark: #3c3c3c;
    --on-blue: #eef2f5;
  }
  html, body {
    margin: 0;
    padding: 0;
    width: 1200px;
    height: 1000px;
    overflow: hidden;
    background: var(--backdrop);
    font-family: "Barlow", sans-serif;
  }
  .canvas {
    position: relative;
    width: 1200px;
    height: 1000px;
  }
  .wordmark {
    position: absolute;
    display: flex;
    align-items: center;
    gap: 4px;
    font-family: "Barlow", sans-serif;
    font-weight: 700;
    letter-spacing: 0.5px;
    line-height: 1;
  }
  .wordmark .mark-square {
    display: inline-block;
    width: 13px;
    height: 13px;
    background: currentColor;
  }

  /* Business card — front */
  .card-front {
    position: absolute;
    left: 89px;
    top: 96px;
    width: 369px;
    height: 210px;
    background: linear-gradient(120deg, var(--brand-blue-deep) 0%, var(--brand-blue) 45%, var(--brand-blue-light) 100%);
  }
  .card-front .wordmark {
    right: 24px;
    top: 153px;
    font-size: 20px;
    color: var(--on-blue);
  }
  .card-front .web {
    position: absolute;
    right: 42px;
    top: 271px;
    top: 175px;
    font-size: 10px;
    font-weight: 600;
    color: var(--on-blue);
  }

  /* Business card — back */
  .card-back {
    position: absolute;
    left: 89px;
    top: 341px;
    width: 369px;
    height: 210px;
    background: var(--paper);
  }
  .card-back .person {
    position: absolute;
    left: 33px;
    top: 62px;
  }
  .card-back .name {
    margin: 0;
    font-size: 13px;
    font-weight: 600;
    color: var(--brand-blue);
  }
  .card-back .position {
    margin: 1px 0 0;
    font-size: 9.5px;
    font-weight: 600;
    color: var(--ink-dark);
  }
  .card-back .contact {
    position: absolute;
    left: 34px;
    top: 104px;
    font-size: 9.5px;
    line-height: 13px;
    color: var(--ink-dark);
  }
  .card-back .contact .phone {
    font-weight: 700;
    color: var(--brand-blue);
  }
  .card-back .address {
    position: absolute;
    left: 34px;
    top: 157px;
    font-size: 8.5px;
    line-height: 12.5px;
    color: var(--ink-dark);
  }
  .card-back .wordmark {
    right: 24px;
    top: 162px;
    font-size: 20px;
    color: var(--ink);
  }

  /* Letterhead */
  .letterhead {
    position: absolute;
    left: 541px;
    top: 93px;
    width: 576px;
    height: 815px;
    background: var(--paper);
  }
  .letterhead .wordmark {
    left: 35px;
    top: 43px;
    font-size: 20px;
    color: var(--ink);
  }
  .letterhead .footer-contact {
    position: absolute;
    left: 34px;
    top: 724px;
    font-size: 13px;
    line-height: 17px;
    color: var(--ink);
  }
  .letterhead .footer-contact .phone {
    display: block;
    margin-bottom: 5px;
    font-weight: 700;
    color: var(--brand-blue);
  }
  .letterhead .footer-web {
    position: absolute;
    right: 40px;
    top: 761px;
    font-size: 13px;
    color: var(--ink);
  }
  .letterhead .footer-web strong {
    font-weight: 700;
    color: var(--brand-blue);
  }
</style>
</head>
<body>
<main class="canvas">

  <section class="card-front" role="img" aria-label="Business card front: blue gradient background with brand name and web address">
    <div class="wordmark"><span class="mark-square"></span>RTAVENOR</div>
    <div class="web">www.rtavenor.com</div>
  </section>

  <section class="card-back">
    <div class="person">
      <p class="name">Name Surname</p>
      <p class="position">Position</p>
    </div>
    <div class="contact">
      <div class="phone">919-555-0148</div>
      <div>name@rtavenor.com</div>
      <div>rtavenor.com</div>
    </div>
    <div class="address">
      <div>4187 Marlowe Ct. Apex</div>
      <div>North Carolina 27614</div>
    </div>
    <div class="wordmark"><span class="mark-square"></span>RTAVENOR</div>
  </section>

  <section class="letterhead">
    <div class="wordmark"><span class="mark-square"></span>RTAVENOR</div>
    <div class="footer-contact">
      <span class="phone">919-555-0148</span>
      <div>4187 Marlowe Ct. Apex</div>
      <div>North Carolina 27614</div>
    </div>
    <div class="footer-web"><strong>rtavenor</strong>.com</div>
  </section>

</main>
</body>
</html>
```